Animal Eye Clinic needs a Business card

We are a new veterinary ophthalmology practice (Ridgeline Pet Vision Care) and we need a business card designed. We only see animal eyes - we are not a regular veterinary clinic. We already have a logo. We are looking for a professional, good looking business card to hand out to our clients. We are looking for something simple but professional and contemporary. Our logo is likely the only picture/graphic that needs to be on the card.
Updates

Contact Information for Business Card

Delia Vossman, BSc, DVM, MSc, DipACVO
Veterinary Ophthalmologist

Phone: 250.418.3927
Email: ridgelinepetvisioncare@mailbox-example.net
Website: ridgelinepetvisioncare-example.net
Address: 1874 Thornbury Rd
Kelowna, BC, V1X 4M9

Colors

Designer to choose colors to be used in the design.

Requirements
Must have
• Our logo (attached)

```html
<!DOCTYPE html>
<html lang="en">
<head>
<meta charset="utf-8">
<title>Ridgeline Pet Vision Care – Business Card</title>
<link rel="stylesheet" href="https://fonts.googleapis.com/css2?family=Arimo:wght@400;700&display=swap">
<style>
  :root {
    --backdrop: #3a3c3f;
    --card: #242223;
    --teal: #1c9aa9;
    --text-light: #f2f2f2;
    --text-soft: #d9d9d9;
  }
  * { margin: 0; padding: 0; box-sizing: border-box; }
  html, body {
    width: 1200px; height: 900px; overflow: hidden;
    background: var(--backdrop);
    font-family: "Arimo", Arial, sans-serif;
  }
  .stage { position: relative; width: 1200px; height: 900px; }
  .card {
    position: absolute;
    width: 560px; height: 320px;
    background: var(--card);
    box-shadow: 0 14px 30px rgba(0,0,0,.45);
  }
  .card--front { left: 70px; top: 90px; }
  .card--back { left: 570px; top: 480px; }

  .brand { position: absolute; display: flex; align-items: center; gap: 12px; }
  .brand__dot { width: 34px; height: 34px; border-radius: 50%; background: var(--teal); flex: none; }
  .brand__name {
    color: var(--teal); font-weight: 700; font-size: 22px;
    text-transform: uppercase; letter-spacing: .5px; line-height: 1.1;
    white-space: nowrap;
  }
  .card--front .brand { left: 90px; top: 128px; }

  .web {
    position: absolute; left: 0; right: 0; top: 252px;
    display: flex; justify-content: center; align-items: center; gap: 7px;
    color: var(--text-light); font-size: 13px;
  }
  .icon {
    width: 14px; height: 14px; border-radius: 50%; background: var(--teal);
    display: inline-flex; align-items: center; justify-content: center; flex: none;
  }
  .icon svg { width: 9px; height: 9px; }

  .card--back .brand { left: 36px; top: 122px; gap: 10px; }
  .card--back .brand__dot { width: 30px; height: 30px; }
  .card--back .brand__name { font-size: 17px; }

  .person { position: absolute; right: 34px; top: 24px; text-align: right; }
  .person__name {
    color: var(--teal); font-weight: 700; font-size: 20px;
    font-variant: small-caps; letter-spacing: 1.5px;
  }
  .person__meta { color: var(--text-light); font-size: 11.5px; line-height: 1.45; margin-top: 4px; }
  .rule { position: absolute; height: 2px; background: var(--teal); }
  .rule--name { left: 370px; right: 24px; top: 100px; }
  .rule--contact { left: 30px; right: 190px; top: 286px; }

  .contacts { position: absolute; left: 44px; top: 220px; color: var(--text-light); }
  .contacts__row { display: flex; align-items: center; gap: 6px; font-size: 12.5px; margin-bottom: 8px; }
  .contacts__phone { font-size: 15px; }
  .contacts__gap { width: 8px; }
</style>
</head>
<body>
<main class="stage">
  <section class="card card--front" aria-label="Business card front">
    <div class="brand">
      <span class="brand__dot"></span>
      <span class="brand__name">Ridgeline Pet Vision Care</span>
    </div>
    <p class="web">
      <span class="icon"><svg viewBox="0 0 10 10"><circle cx="5" cy="5" r="4" fill="none" stroke="#242223" stroke-width="1"/><path d="M1 5h8M5 1c-2 2.5-2 5.5 0 8M5 1c2 2.5 2 5.5 0 8" fill="none" stroke="#242223" stroke-width=".8"/></svg></span>
      ridgelinepetvisioncare-example.net
    </p>
  </section>

  <section class="card card--back" aria-label="Business card back">
    <div class="person">
      <h1 class="person__name">Delia Vossman</h1>
      <p class="person__meta">BSc, DVM, MSc, DipACVO<br>Veterinary Ophthalmologist</p>
    </div>
    <div class="rule rule--name"></div>

    <div class="brand">
      <span class="brand__dot"></span>
      <span class="brand__name">Ridgeline Pet Vision Care</span>
    </div>

    <div class="contacts">
      <p class="contacts__row">
        <span class="icon"><svg viewBox="0 0 10 10"><path d="M2.5 1.5l1.5 2-1 1c.6 1.2 1.3 1.9 2.5 2.5l1-1 2 1.5-1 1.5C5 9 1 5 1 2.5z" fill="#242223"/></svg></span>
        <span class="contacts__phone">250.418.3927</span>
        <span class="contacts__gap"></span>
        <span class="icon"><svg viewBox="0 0 10 10"><path d="M5 9.5S2 6 2 4a3 3 0 016 0c0 2-3 5.5-3 5.5z" fill="#242223"/><circle cx="5" cy="4" r="1" fill="#1c9aa9"/></svg></span>
        <span>1874 Thornbury Rd, Kelowna, BC, V1X 4M9</span>
      </p>
      <p class="contacts__row">
        <span class="icon"><svg viewBox="0 0 10 10"><rect x="1.5" y="2.5" width="7" height="5" fill="#242223"/><path d="M1.5 2.5L5 5.5l3.5-3" fill="none" stroke="#1c9aa9" stroke-width=".8"/></svg></span>
        <span>ridgelinepetvisioncare@mailbox-example.net</span>
      </p>
    </div>
    <div class="rule rule--contact"></div>
  </section>
</main>
</body>
</html>
```